Business card for medical clinic

I need an upmarket, modern medical/health business card for my clinic

Contact Information for Business Card

name, address, email, qr code

```html
<!DOCTYPE html>
<html lang="en">
<head>
<meta charset="utf-8">
<title>Meridian Care Clinic – Business Card</title>
<link rel="stylesheet" href="https://fonts.googleapis.com/css2?family=Cinzel:wght@400&family=Arimo:wght@400&display=swap">
<style>
  :root {
    --stage: #3d3d3d;
    --paper: #ffffff;
    --navy: #17294f;
    --navy-deep: #13203f;
    --sky: #0aa6e6;
    --sky-mid: #0b7fc0;
    --ink: #2b2b2b;
    --ink-soft: #555a63;
    --brand-blue: #1d5a9c;
    --silver: #a9a9ad;
  }
  * { box-sizing: border-box; margin: 0; padding: 0; }
  html, body { width: 1200px; height: 803px; overflow: hidden; background: var(--stage); }
  .stage {
    width: 1200px; height: 803px;
    display: flex; align-items: center; justify-content: center; gap: 44px;
  }
  .card {
    position: relative;
    width: 540px; height: 309px;
    border-radius: 16px;
    overflow: hidden;
    box-shadow: 0 14px 30px rgba(0,0,0,.35);
  }

  /* Front */
  .card--front { background: var(--paper); }
  .brand {
    display: flex; align-items: center; gap: 10px;
    font-family: "Arimo", sans-serif; font-weight: 400;
    color: var(--brand-blue);
  }
  .card--front .brand {
    position: absolute; left: 40px; top: 108px; width: 210px;
  }
  .brand__mark {
    width: 12px; height: 12px; background: currentColor; flex: none;
  }
  .brand__name { font-size: 17px; line-height: 1.25; letter-spacing: .5px; }
  .divider {
    position: absolute; left: 268px; top: 40px;
    width: 1px; height: 170px;
    background: linear-gradient(to bottom, transparent, #cfd3d8 30%, #cfd3d8 70%, transparent);
  }
  .contact {
    position: absolute; left: 292px; top: 44px;
    font-family: "Arimo", sans-serif; color: var(--ink);
  }
  .contact__name {
    font-family: "Cinzel", serif; font-weight: 400;
    font-size: 21px; color: var(--navy); letter-spacing: 1px;
  }
  .contact__title { font-size: 11px; color: var(--ink-soft); margin-top: 1px; }
  .contact__address { font-size: 11.5px; line-height: 1.4; margin-top: 14px; }
  .contact__list { list-style: none; margin-top: 10px; font-size: 11.5px; line-height: 1.55; }
  .contact__list li { display: flex; align-items: center; gap: 7px; }
  .contact__list svg { width: 11px; height: 11px; fill: var(--navy); flex: none; }

  .band {
    position: absolute; left: 0; bottom: 14px;
    width: 100%; height: 38px;
    background: linear-gradient(90deg, var(--navy-deep) 0%, var(--sky-mid) 30%, var(--sky) 48%, var(--sky-mid) 66%, var(--navy) 88%);
    display: flex; align-items: center; padding-left: 44px;
  }
  .band__url { font-family: "Arimo", sans-serif; font-size: 12.5px; color: #fff; letter-spacing: .3px; }
  .band__tail {
    position: absolute; right: 0; top: 0; height: 100%; width: 64px;
    background: linear-gradient(90deg, #d6d6d8, var(--silver));
  }
  .band__dot {
    position: absolute; right: 50px; top: 50%;
    width: 28px; height: 28px; margin-top: -14px;
    border-radius: 50%; background: #fff; border: 2px solid var(--sky-mid);
  }

  /* Back */
  .card--back {
    background: radial-gradient(ellipse 60% 70% at 42% 55%, var(--sky) 0%, var(--sky-mid) 35%, #11406f 70%, var(--navy) 100%);
    display: flex; align-items: center; justify-content: center;
  }
  .card--back .brand { color: #fff; gap: 16px; }
  .card--back .brand__mark { width: 18px; height: 18px; }
  .card--back .brand__name { font-size: 32px; letter-spacing: 1px; line-height: 1.2; }
</style>
</head>
<body>
<main class="stage">
  <article class="card card--front" aria-label="Card front">
    <div class="brand">
      <span class="brand__mark"></span>
      <span class="brand__name">Meridian Care<br>Clinic</span>
    </div>
    <div class="divider"></div>
    <div class="contact">
      <h1 class="contact__name">DANIEL HART</h1>
      <p class="contact__title">President</p>
      <p class="contact__address">4120 Juniper Court<br>Fairview, Canada 58210</p>
      <ul class="contact__list">
        <li><svg viewBox="0 0 24 24"><path d="M6.6 10.8a15 15 0 0 0 6.6 6.6l2.2-2.2c.3-.3.7-.4 1-.2 1.1.4 2.3.6 3.6.6.6 0 1 .4 1 1V20c0 .6-.4 1-1 1A17 17 0 0 1 3 4c0-.6.4-1 1-1h3.5c.6 0 1 .4 1 1 0 1.3.2 2.5.6 3.6.1.3 0 .7-.2 1z"/></svg>555-210-4871</li>
        <li><svg viewBox="0 0 24 24"><path d="M7 1h10a2 2 0 0 1 2 2v18a2 2 0 0 1-2 2H7a2 2 0 0 1-2-2V3a2 2 0 0 1 2-2zm0 3v14h10V4z"/></svg>555-382-6094</li>
        <li><svg viewBox="0 0 24 24"><path d="M2 5h20v14H2zm2 2v.5l8 5 8-5V7z"/></svg>hello@meridiancare.com</li>
      </ul>
    </div>
    <div class="band">
      <span class="band__url">www.meridiancare.com</span>
      <span class="band__tail"></span>
      <span class="band__dot"></span>
    </div>
  </article>

  <article class="card card--back" aria-label="Card back">
    <div class="brand">
      <span class="brand__mark"></span>
      <span class="brand__name">Meridian Care<br>Clinic</span>
    </div>
  </article>
</main>
</body>
</html>
```